Clear Plastic Card Design

I am looking to have a business card designed from my logo icon. I am looking to match the style of a different business card I have attached in the files.
Looking for a card that is plastic, with layers of transparency in the shape of my logo icon (also attached in the files) - not a circle like the other card. The winning design will incorporate the red icon logo on the front and back and include the charity's name, "Light for the Weary Souls" in the same or similar font, as well as an email and phone number. For now, use the email: email@lightfortheweary-mail.org and the phone number 555-382-7194.
We like how the sample business card has transparency, partial and full opacity layers and a matching color scheme. Files will need to be in vector so that our business card printing company can work with it.
UPDATE:
We've some excellent designs in, thank you everyone! I got an early review from the owner, and he requested a minor redirect to find his perfect design. He wants the design to stand out by NOT being a rectangle. Try instead a circle, square, or best yet - something that falls in the outline of the logo icon, either fully or partially. Thank you, everyone!
Light for the Weary Souls text should be incorporated as well as a phone and email.

```html
<!DOCTYPE html>
<html lang="en">
<head>
<meta charset="utf-8">
<title>Light for the Weary Souls – Business Card</title>
<link rel="stylesheet" href="https://fonts.googleapis.com/css2?family=Open+Sans:wght@600;700;800&display=swap">
<style>
  :root {
    --page-top: #efe6e4;
    --page-bottom: #e4d9d6;
    --card-fill: rgba(255, 255, 255, 0.55);
    --card-edge: rgba(255, 255, 255, 0.9);
    --brand-red: #c0121c;
    --brand-red-deep: #a80d17;
    --brand-orange: #e8461c;
    --mark-light: rgba(240, 90, 30, 0.78);
    --mark-dark: rgba(200, 16, 40, 0.85);
    --rule-red: #c8141e;
    --contact-grey: #444044;
    --heart-light: #ff5a63;
    --heart-dark: #d3101f;
  }
  * { box-sizing: border-box; margin: 0; padding: 0; }
  html, body {
    width: 1200px;
    height: 900px;
    overflow: hidden;
    background: linear-gradient(180deg, var(--page-top), var(--page-bottom));
    font-family: "Open Sans", Arial, sans-serif;
  }
  .card {
    position: absolute;
    left: 60px;
    top: 117px;
    width: 1080px;
    height: 666px;
  }
  .card-shape {
    position: absolute;
    inset: 0;
    width: 1080px;
    height: 666px;
    filter: drop-shadow(0 10px 30px rgba(120, 60, 60, 0.14));
  }
  .brand-mark {
    position: absolute;
    left: 130px;
    top: 140px;
    width: 300px;
    height: 300px;
    border-radius: 18px;
    background: linear-gradient(135deg, var(--mark-light), var(--mark-dark));
  }
  .card-title {
    position: absolute;
    left: 505px;
    top: 208px;
    width: 510px;
    text-align: center;
    color: var(--brand-red);
    font-weight: 800;
    font-size: 58px;
    line-height: 70px;
    text-transform: uppercase;
    letter-spacing: -0.5px;
  }
  .card-title .line-two { color: var(--brand-red-deep); }
  .divider {
    position: absolute;
    left: 54px;
    top: 525px;
    width: 940px;
    height: 3px;
    background: var(--rule-red);
  }
  .heart-art {
    position: absolute;
    left: 923px;
    top: 392px;
    width: 167px;
    height: 150px;
    border-radius: 50% 50% 46% 46%;
    background: radial-gradient(circle at 40% 35%, var(--heart-light), var(--heart-dark));
  }
  .contact {
    position: absolute;
    top: 564px;
    display: flex;
    align-items: center;
    gap: 10px;
    color: var(--contact-grey);
    font-weight: 600;
  }
  .contact-phone { left: 52px; font-size: 40px; }
  .contact-email { left: 426px; font-size: 30px; }
  .contact-icon { width: 48px; height: 48px; flex: none; }
</style>
</head>
<body>
  <div class="card">
    <svg class="card-shape" viewBox="0 0 1080 666" aria-hidden="true">
      <path d="M110 0 L1036 0 Q1080 0 1080 44 L1080 622 Q1080 666 1036 666 L44 666 Q0 666 0 622 L0 110 Z"
            fill="var(--card-fill)" stroke="var(--card-edge)" stroke-width="3"/>
    </svg>

    <div class="brand-mark"></div>

    <h1 class="card-title">
      <span class="line-one">Light for the</span><br>
      <span class="line-two">Weary Souls</span>
    </h1>

    <div class="heart-art" role="img" aria-label="Red cracked heart illustration"></div>

    <div class="divider"></div>

    <div class="contact contact-phone">
      <svg class="contact-icon" viewBox="0 0 48 48" aria-hidden="true">
        <circle cx="24" cy="24" r="23" fill="var(--brand-orange)"/>
        <circle cx="24" cy="24" r="20" fill="var(--rule-red)"/>
        <path d="M16 14c1.5-1.5 3-1.5 4 0l2.5 3.5c.8 1.2.5 2.3-.5 3.2l-1.5 1.3c1 2.5 3 4.5 5.5 5.5l1.3-1.5c.9-1 2-1.3 3.2-.5L34 28c1.5 1 1.5 2.5 0 4l-2 2c-2 2-7 1-12-4s-6-10-4-12z" fill="#fff"/>
      </svg>
      <span>555-382-7194</span>
    </div>

    <div class="contact contact-email">
      <svg class="contact-icon" viewBox="0 0 48 48" aria-hidden="true">
        <circle cx="24" cy="24" r="23" fill="var(--brand-orange)"/>
        <circle cx="24" cy="24" r="20" fill="var(--rule-red)"/>
        <rect x="13" y="16" width="22" height="16" rx="1.5" fill="#fff"/>
        <path d="M13.5 17 24 25.5 34.5 17" fill="none" stroke="var(--rule-red)" stroke-width="1.8"/>
      </svg>
      <span>email@lightfortheweary-mail.org</span>
    </div>
  </div>
</body>
</html>
```